Website for a Psychologist in Private Practice

I need a cool web design for my website: www.drkalvoric.com. I would like it to look professional. Keep all the current content and add: Space for video; radio spots (see Silver Cedar Tunes Logo below for those); Quick Inquiry; Friendora link; 5 star rating on Rivo; a map; reviews from former patients. I am open to suggestions.

Target Market(s)

Those seeking individual and marital counseling.

Industry/Entity Type

Mental Health

Number of Pages Required

1 page

Font styles to use
Sans Serif
Other font styles liked:
• I'm open but no hard to read script

Requirements
Must have
• All the content on my home page with link for video and radio spots. List services and degrees and expertices (pics not necessary).
Nice to have
• A video of me and radio conversations (logo of Silver Cedar Tunes radio attached).
Should not have
• Cartoons, comedy, etc.... I don't need pictures of services (marital, depression, etc...) Just list those.

```html
<!DOCTYPE html>
<html lang="en">
<head>
<meta charset="utf-8">
<title>Dr. Mara L. Kalvoric – Clinical Psychologist</title>
<link href="https://fonts.googleapis.com/css2?family=Arimo:wght@400;700&family=Vollkorn:wght@400;500&family=Great+Vibes&display=swap" rel="stylesheet">
<style>
  :root {
    --gold: #c9ad52;
    --gold-soft: #d9c277;
    --ink: #1d1d1d;
    --text: #555555;
    --muted: #777777;
    --rule: #cfcfcf;
    --panel: #f3f3f3;
    --arrow-box: #d3d3d3;
    --white: #ffffff;
  }
  * { box-sizing: border-box; margin: 0; padding: 0; }
  html, body { width: 934px; height: 1200px; overflow: hidden; background: var(--white); }
  body { position: relative; font-family: "Arimo", Arial, sans-serif; color: var(--text); }

  .hero {
    position: absolute; left: 0; top: 0; width: 934px; height: 203px;
    background: linear-gradient(180deg, #6b6650 0%, #8d8566 35%, #5d5a48 60%, #8a7f61 85%, #a49675 100%);
  }
  .hero-title {
    position: absolute; left: 0; top: 52px; width: 934px; text-align: center;
    font-family: "Great Vibes", cursive; font-size: 56px; color: var(--gold-soft);
  }
  .role-badge {
    position: absolute; left: 274px; top: 174px; width: 386px; height: 54px;
    background: var(--white); padding: 4px 4px 0 4px;
  }
  .role-badge span {
    display: block; height: 50px; background: var(--gold); color: var(--white);
    font-family: "Vollkorn", serif; font-size: 25px; letter-spacing: 1px;
    text-align: center; line-height: 50px;
  }
  .license { position: absolute; left: 0; top: 235px; width: 934px; text-align: center; font-size: 12.5px; color: var(--muted); }

  .main-nav {
    position: absolute; left: 0; top: 275px; width: 934px; text-align: center;
    font-family: "Vollkorn", serif; font-size: 13.5px; color: var(--ink); letter-spacing: .5px;
  }
  .main-nav a { color: var(--ink); text-decoration: none; }
  .main-nav a.active { color: var(--gold); }
  .main-nav .sep { margin: 0 26px; }
  .rule { position: absolute; left: 60px; width: 814px; height: 1px; background: var(--rule); }

  .intro {
    position: absolute; left: 60px; top: 345px; width: 814px;
    font-size: 11px; line-height: 19.5px; color: var(--text);
  }
  .portrait {
    float: left; width: 186px; height: 186px; margin: 4px 39px 16px 0;
    background: linear-gradient(135deg, #6d8a3c 0%, #a7b36a 40%, #5578a8 80%, #3e5f90 100%);
  }
  .intro p { text-indent: 21px; }
  .intro p:first-of-type { text-indent: 3px; }
  .intro p.plain { text-indent: 0; }
  .intro strong { font-weight: 400; color: #333; }

  .radio-head {
    position: absolute; left: 60px; top: 697px; width: 454px; height: 49px;
    background: var(--gold); color: var(--white);
    font-family: "Vollkorn", serif; font-size: 24px; letter-spacing: 1px;
    line-height: 49px; padding-left: 27px;
  }
  .radio-item { position: absolute; left: 60px; width: 454px; height: 41px; }
  .radio-item h3 { font-family: "Vollkorn", serif; font-weight: 400; font-size: 15px; color: var(--ink); position: absolute; left: 2px; top: -2px; }
  .radio-item time { position: absolute; left: 2px; top: 24px; font-size: 11.5px; color: var(--text); }
  .radio-item .play-arrow { position: absolute; right: 0; top: 0; width: 41px; height: 41px; background: var(--arrow-box); }

  .donate-note { position: absolute; left: 62px; top: 980px; font-family: "Vollkorn", serif; font-size: 14.5px; color: var(--gold); }
  .partner { position: absolute; top: 1010px; height: 48px; background: #e9e9e9; }

  .video-frame {
    position: absolute; left: 566px; top: 697px; width: 308px; height: 203px;
    background: radial-gradient(circle at 50% 60%, #f3dfa1 0%, #deba6a 55%, #caa14f 100%);
  }
  .video-frame svg { position: absolute; left: 130px; top: 78px; }

  .signup { position: absolute; left: 566px; top: 916px; width: 308px; height: 146px; background: var(--panel); }
  .signup p { position: absolute; left: 0; top: 23px; width: 308px; text-align: center; font-size: 11.5px; line-height: 18px; color: #444; }
  .signup .email-field {
    position: absolute; left: 16px; top: 81px; width: 276px; height: 37px;
    background: var(--white); border: 1px solid #cccccc;
    font-size: 11px; color: #999; line-height: 35px; padding-left: 13px;
  }
  .signup .email-field svg { position: absolute; right: 12px; top: 13px; }

  .site-footer { position: absolute; left: 0; top: 1121px; width: 934px; text-align: center; font-size: 11px; line-height: 18px; color: var(--text); }
  .site-footer .bar { margin: 0 10px; }
  .copyright { position: absolute; left: 0; top: 1172px; width: 934px; text-align: center; font-size: 10.5px; color: #333; }
  .copyright span { color: var(--gold); }
  .social { position: absolute; right: 60px; top: 1171px; font-size: 10px; color: var(--gold); }
  .social span { margin-left: 8px; }
</style>
</head>
<body>

<header>
  <div class="hero" role="img" aria-label="Beach at sunset with two people walking along the shoreline"></div>
  <div class="hero-title">Dr. Mara L. Kalvoric</div>
  <div class="role-badge"><span>CLINICAL PSYCHOLOGIST</span></div>
  <div class="license">California # PSY20583</div>
  <nav class="main-nav">
    <a class="active" href="#">HOME</a><span class="sep">/</span><a href="#">SESSIONS</a><span class="sep">/</span><a href="#">RESOURCES</a><span class="sep">/</span><a href="#">BIO</a><span class="sep">/</span><a href="#">CONTACT</a>
  </nav>
  <div class="rule" style="top:308px"></div>
</header>

<section class="intro">
  <div class="portrait" role="img" aria-label="Portrait photo of the psychologist"></div>
  <p>I'm so glad you are here.&nbsp; Choosing to see a professional for issues in your life can be difficult but also possibly life changing.&nbsp; Many postpone seeking help because they believe doing so acknowledges failure on their part.&nbsp; Reallly? We seek the help of experts all the time (contractors, mechanics, chefs, etc...) and what is more important than your life? Consulting with a neutral party to act in your best interest can be time well spent.&nbsp; So if you are willing to take the time to invest in counseling, make sure that it is with someone that is worth your time.</p>
  <p>Choose a licensed psychologist with a doctoral degree (Ph.D. or PsyD.) - both have over 10 years of education in the field of psychology, extensive internships and comprehensive licensing exams.&nbsp; Others have far less education if any.&nbsp; Also, consider tthe therapist's approach to therapy.&nbsp; I use a straightforward approach (psychobabble available upon request) with brief, solution-oriented sessions.</p>
  <p>Experience also separates good psychologists from others with fewer and more proficient sessions. My&nbsp; 20+ years of professional experience and my life experience contributes to the empathetic perspective I use to relate to each person I see.&nbsp; I also believe it is the reason 90% of my practice is referral based and why many other psychologists in the area seek my services.</p>
  <p class="plain"><strong>DO NOT COMPROMISE</strong>.&nbsp; Find an educated, licensed, experienced professional that you can relate to. Think about what it took to get you here and the importance resolving this issue can have on your life.</p>
</section>

<div class="rule" style="top:657px"></div>

<section>
  <div class="radio-head">RADIO CONVERSION LINKS</div>
  <article class="radio-item" style="top:770px">
    <h3>Lorem ipsum is simply dummy text of the printing</h3>
    <time>Feb 20, 2016</time>
    <div class="play-arrow"><svg width="41" height="41"><polyline points="18,14 25,20.5 18,27" fill="none" stroke="#fff" stroke-width="2.5"/></svg></div>
  </article>
  <article class="radio-item" style="top:835px">
    <h3>Lorem ipsum is simply dummy text of the printing</h3>
    <time>Feb 20, 2016</time>
    <div class="play-arrow"><svg width="41" height="41"><polyline points="18,14 25,20.5 18,27" fill="none" stroke="#fff" stroke-width="2.5"/></svg></div>
  </article>
  <article class="radio-item" style="top:900px">
    <h3>Lorem ipsum is simply dummy text of the printing</h3>
    <time>Feb 20, 2016</time>
    <div class="play-arrow"><svg width="41" height="41"><polyline points="18,14 25,20.5 18,27" fill="none" stroke="#fff" stroke-width="2.5"/></svg></div>
  </article>

  <div class="donate-note">A portion of all revenue is donated to</div>
  <div class="partner" style="left:60px;width:94px"></div>
  <div class="partner" style="left:170px;width:126px"></div>
  <div class="partner" style="left:335px;width:180px"></div>
</section>

<aside>
  <div class="video-frame" role="img" aria-label="Video still of cupped hands holding golden light">
    <svg width="48" height="48" viewBox="0 0 48 48"><circle cx="24" cy="24" r="23" fill="none" stroke="#fff" stroke-width="1.5"/><polygon points="19,15 33,24 19,33" fill="#fff"/></svg>
  </div>
  <div class="signup">
    <p>Sign up with your email address to<br>receive news and updates!</p>
    <div class="email-field">E-Mail
      <svg width="18" height="12" viewBox="0 0 18 12"><rect x="0.5" y="0.5" width="17" height="11" fill="none" stroke="#c9ad52"/><polyline points="0.5,0.5 9,7 17.5,0.5" fill="none" stroke="#c9ad52"/></svg>
    </div>
  </div>
</aside>

<div class="rule" style="top:1103px"></div>

<footer>
  <div class="site-footer">
    Dr. Mara L. Kalvoric<span class="bar">|</span>418 Harbor Crest Way, Suite 210 Bayview, CA 90000<span class="bar">|</span><br>
    (555) 014 2231<span class="bar">|</span>mk@drkalvoric.com
  </div>
  <div class="copyright">© <span>drkalvoric</span> – 2016. All Rights reserved.</div>
  <div class="social"><span>Friendora</span><span>Chirply</span><span>Plusora</span></div>
</footer>

</body>
</html>
```